Novexa company website, a website for employment for people with autism

The website will make a match between people and jobs, mainly in the graphical sector, but also other sectors.
The name of the company is novexa and automates jobs with people that are on the autism spectrum.
The whole matchmaking and feedback process and so doesn't have to be in this prototype, we just want the general information pages and to convey a great look and brand identity that we will keep in the other pages to be developed. The website must be made with Wordpress, since the backend will be developed in Wordpress too.
It is a social project that wants to create possibilites for people with ASS to work from home for an employer or to do a variety of tasks for different customers.
The people we hire are generally not on the regular job market or have difficulty finding a job and "selling themselves"

Target Market(s)

matchmaking between talent (with ASS) and employers / jobs

Number of Pages Required

5+ page

Font styles to use
Sans Serif

Colors
ec1f27
e34298
a64599
6b449b
0355a3
0792cd

Requirements
Must have
• A stunning landing pages
• Integrate our logo and must match with what will do. We want a clean, modern, minimalistic, sleek website that radiates creativity and good looks.
• We have one page describing what we can do for customers, one page for people with ASS that would like to be candidates (our approach, learning program, ...), two pages that are addressed to partners who want to cooperate: the one's that can assist with autism related assistance and the one's that can help with the job coaching.
Nice to have
• In our logo are many colors as we embrace diversity and want to show that. Out main branding colors are red (for action) and blue for stability and will all gradients that go with it. Mainly white or black (or anthracite) for other parts
Should not have
• We want a modern and minimalistic design, no fluffy designs with lots of ornaments.

```html
<!DOCTYPE html>
<html lang="en">
<head>
<meta charset="utf-8">
<title>Novexa</title>
<link href="https://fonts.googleapis.com/css2?family=Montserrat:wght@400;500;600&family=Open+Sans:wght@400;600;700&display=swap" rel="stylesheet">
<style>
:root{
  --red:#ec1f27;
  --pink:#e34298;
  --violet:#a64599;
  --purple:#6b449b;
  --blue:#0355a3;
  --sky:#0792cd;
  --frame-blue:#1a7fc6;
  --band-blue:#0a4ea6;
  --ring-pink:#f4bcc3;
  --ink:#222428;
  --text:#555a60;
  --white:#ffffff;
}
*{margin:0;padding:0;box-sizing:border-box}
html,body{width:1200px;height:2449px;overflow:hidden;background:var(--white)}
body{position:relative;font-family:"Open Sans",Arial,sans-serif;color:var(--text)}
.abs{position:absolute}

/* hero */
.hero{left:0;top:0;width:1200px;height:668px;
  background:
    radial-gradient(ellipse 420px 320px at 600px 300px, rgba(150,90,200,.55), transparent 70%),
    radial-gradient(ellipse 500px 500px at 1150px 60px, rgba(7,146,205,.8), transparent 70%),
    radial-gradient(ellipse 420px 500px at 0px 560px, rgba(180,30,60,.55), transparent 70%),
    linear-gradient(180deg,#4a2a6e 0%,#2c1a4e 55%,#150b22 100%);}
.brand{left:114px;top:94px;display:flex;align-items:center;gap:14px}
.brand-mark{width:26px;height:26px;border-radius:50%;background:var(--white)}
.brand-name{font-family:"Montserrat",Arial,sans-serif;font-weight:500;font-size:30px;letter-spacing:3px;color:var(--white)}
.menu-toggle{left:1050px;top:73px;width:40px;height:28px}
.menu-toggle span{position:absolute;left:0;width:40px;height:3px;background:var(--white)}
.hero-title{left:0;top:200px;width:1200px;text-align:center;font-family:"Montserrat",Arial,sans-serif;font-weight:500;font-size:86px;letter-spacing:26px;color:var(--white);padding-left:26px}
.hero-lead{left:200px;top:328px;width:800px;text-align:center;font-size:22px;line-height:38px;color:var(--white)}
.hero-btn{left:496px;top:442px;width:209px;height:64px;border:2px solid var(--white);color:var(--white);font-weight:700;font-size:18px;display:flex;align-items:center;justify-content:center;letter-spacing:.5px}
.hero-play{left:584px;top:560px}

/* welcome */
.welcome-frame{left:111px;top:854px;width:408px;height:452px;border:10px solid var(--frame-blue)}
.kicker{font-family:"Montserrat",Arial,sans-serif;font-weight:500;font-size:33px;color:var(--ink);letter-spacing:1px}
.headline{font-family:"Montserrat",Arial,sans-serif;font-weight:500;font-size:66px;color:var(--ink);letter-spacing:1px}
.welcome-kicker{left:165px;top:904px}
.welcome-title{left:163px;top:944px}
.body-copy{font-size:15.5px;line-height:31px;width:460px}
.welcome-copy{left:165px;top:1048px;color:var(--text)}
.btn-outline{height:53px;width:166px;border-radius:27px;display:flex;align-items:center;justify-content:center;font-weight:700;font-size:17px}
.welcome-btn{left:165px;top:1203px;border:2px solid var(--red);color:var(--red)}
.photo-ring{left:675px;top:764px;width:496px;height:496px;border-radius:50%;background:var(--ring-pink)}
.photo-main{left:704px;top:793px;width:438px;height:438px;border-radius:50%;background:linear-gradient(135deg,#d9d9d9,#8a8a8a)}
.photo-small{left:629px;top:1132px;width:294px;height:294px;border-radius:50%;background:linear-gradient(135deg,#cfcfcf,#4a4a4a)}

/* who we are */
.who{left:0;top:1538px;width:1200px;height:570px;background:radial-gradient(ellipse 600px 400px at 900px 250px,#0d58b5,var(--band-blue))}
.who-frame{left:87px;top:1635px;width:391px;height:377px;border:10px solid var(--white)}
.who-photo{left:111px;top:1661px;width:478px;height:326px;background:linear-gradient(90deg,#c9a58a,#e6d6c6 55%,#d9c3b0)}
.who-play{left:317px;top:1788px}
.who-kicker{left:647px;top:1646px;color:var(--white)}
.who-title{left:645px;top:1686px;color:var(--white)}
.who-copy{left:647px;top:1786px;color:var(--white)}
.who-btn{left:647px;top:1940px;border:2px solid var(--white);color:var(--white)}

/* footer */
.social{left:487px;top:2214px;display:flex;gap:6px}
.social span{width:52px;height:52px;border-radius:50%;border:1.5px solid #8a8d92}
.contact{left:0;top:2302px;width:1200px;text-align:center;font-size:15.5px;color:var(--text);display:flex;justify-content:center;align-items:center;gap:10px}
.contact svg{vertical-align:middle;margin-right:6px}
.footer-links{left:0;top:2342px;width:1200px;text-align:center;font-size:15px;color:var(--text);word-spacing:2px}
.footer-links span{margin:0 14px}
.copyright{left:0;top:2378px;width:1200px;text-align:center;font-size:15px;color:var(--text)}
</style>
</head>
<body>

<header class="abs hero" role="img" aria-label="Abstract glowing purple and blue backdrop"></header>
<div class="abs brand"><span class="brand-mark"></span><span class="brand-name">NOVEXA</span></div>
<div class="abs menu-toggle" aria-label="Menu"><span style="top:0"></span><span style="top:12px"></span><span style="top:25px"></span></div>
<h1 class="abs hero-title">NOVEXA</h1>
<p class="abs hero-lead">Nam libero tempore, cum soluta nobis est eligendi optio cumque nihil impe quo minus&nbsp; saepe eveniet ut et voluptates repudian sint etm</p>
<div class="abs hero-btn">GET MORE INFO</div>
<svg class="abs hero-play" width="32" height="34" viewBox="0 0 32 34"><polygon points="2,2 30,17 2,32" fill="#fff"/></svg>

<section>
  <div class="abs welcome-frame"></div>
  <div class="abs kicker welcome-kicker">WELCOME TO</div>
  <h2 class="abs headline welcome-title">NOVEXA</h2>
  <p class="abs body-copy welcome-copy">Nam libero tempore, cum soluta nobis est eligendi optio cumque nihil impedit quo minus id quod maxime placeat facere possimus, omnis voluptas assumenda est, omnis dolor repellendu poribuaut em quibusdam et aut officiis debitis.</p>
  <div class="abs btn-outline welcome-btn">READ MORE</div>
  <div class="abs photo-ring"></div>
  <div class="abs photo-main" role="img" aria-label="Black and white photo of two women working together at a table"></div>
  <div class="abs photo-small" role="img" aria-label="Black and white photo of a young man in a wheelchair talking with a caregiver"></div>
</section>

<section>
  <div class="abs who"></div>
  <div class="abs who-frame"></div>
  <div class="abs who-photo" role="img" aria-label="Video still of a girl and a coach talking at a desk"></div>
  <svg class="abs who-play" width="68" height="68" viewBox="0 0 68 68"><circle cx="34" cy="34" r="34" fill="#1b1b1b"/><polygon points="26,20 50,34 26,48" fill="#fff"/></svg>
  <div class="abs kicker who-kicker">WHO</div>
  <h2 class="abs headline who-title">WE ARE</h2>
  <p class="abs body-copy who-copy">Nam libero tempore, cum soluta nobis est eligendi optio cumque nihil impedit quo minus id quod maxime placeat facere possimus, omnis voluptas assumenda est, omnis dolor repellendu poribuaut em quibusdam et aut officiis debitis.</p>
  <div class="abs btn-outline who-btn">READ MORE</div>
</section>

<footer>
  <div class="abs social" aria-label="Social links"><span></span><span></span><span></span><span></span></div>
  <div class="abs contact">
    <span><svg width="12" height="16" viewBox="0 0 12 16"><path d="M6 0a6 6 0 0 0-6 6c0 4.5 6 10 6 10s6-5.5 6-10a6 6 0 0 0-6-6zm0 8.5A2.5 2.5 0 1 1 6 3.5a2.5 2.5 0 0 1 0 5z" fill="#ec1f27"/></svg>Lindenweg 4812 Halvorsted</span>
    <span>|</span>
    <span><svg width="14" height="14" viewBox="0 0 14 14"><path d="M3 0l2.5 3.5-1.5 1.8a8 8 0 0 0 4.7 4.7l1.8-1.5L14 11l-1.5 2.5C6 14 0 8 .5 1.5z" fill="#ec1f27"/></svg>+1 555 014 2276</span>
    <span>|</span>
    <span><svg width="16" height="12" viewBox="0 0 16 12"><rect width="16" height="12" rx="1.5" fill="#ec1f27"/><polyline points="1,1.5 8,7 15,1.5" fill="none" stroke="#fff" stroke-width="1.4"/></svg>info@novexa.be</span>
  </div>
  <div class="abs footer-links">Help<span>|</span>FAQ<span>|</span>Support<span>|</span>Sitemap<span>|</span>Terms Of Use<span>|</span>Privacy Statement</div>
  <div class="abs copyright">Novexa © 2019 All rights reserved.</div>
</footer>

</body>
</html>
```